Agency Website & Personal brand

My name is Petros Vandelis & I've been a digital marketer & an e-commerce expert since 2010.

- I've spoken to 20 different events around the world up to 3,000 people in size.
- I've sold over 1500 training courses around e-commerce growth.
- I have over 100 testimonials (video & photo) from successful students who bought my training
- I have dozens of video testimonials from respected entrepreneurs that vouch for me and my work
- I have photos with marketing legends with that I shared the stage like Omar Lindqvist, Harold Venturini, Kyle Marsh & more
- I am the host of the Aegean Roundtable since 2017 - a high-level networking event for 7 & 8 figure entrepreneurs - 100 people have come to Greece since 2017
- I have tons of videos created where I showcase my expertise on growth
- I have worked with dozens of e-commerce stores on their growth & helped them scale to multiple 6, 7 & 8 figures either on consulting

I need a website design that showcases my authority & be a lead generating machine.

The goal is to bring people on a call with me but also grab their email and start building the relationship with them and free valuable content

We have 3 offers :

1. Paid ads (Done for You)
2. Consulting/Mastermind (Done with You)
3. Training (Do it Yourself)

```html
<!DOCTYPE html>
<html lang="en">
<head>
<meta charset="utf-8">
<title>Petros Vandelis – Growth Marketing</title>
<link href="https://fonts.googleapis.com/css2?family=Roboto:wght@400;500;700&display=swap" rel="stylesheet">
<style>
:root{
  --red:#e2352c;
  --ink:#1f1f1f;
  --text:#555;
  --beige:#f3dcc4;
  --beige-2:#ead0b4;
  --grey-bg:#f4f4f4;
  --footer:#2b2b2b;
  --footer-text:#cfcfcf;
  --white:#fff;
}
*{margin:0;padding:0;box-sizing:border-box}
html,body{width:1200px;height:4104px;overflow:hidden}
body{position:relative;font-family:"Roboto",Arial,sans-serif;color:var(--text);background:var(--white)}
.abs{position:absolute}
.backdrop{position:absolute;left:0;top:0}
/* header */
.brand{left:110px;top:26px;font-size:22px;font-weight:700;color:var(--ink)}
.brand span,.hero-title span{color:var(--red)}
.nav{left:392px;top:32px;display:flex;gap:33px;font-size:14px;font-weight:500;color:var(--ink)}
.nav a{color:inherit;text-decoration:none;padding-bottom:6px}
.nav a.active{color:var(--red);border-bottom:2px solid var(--red)}
.call{left:868px;top:22px;display:flex;align-items:center;gap:14px}
.call-icon{width:40px;height:40px;border-radius:50%;background:var(--white);border:2px solid #f2c9b0;display:flex;align-items:center;justify-content:center}
.call small{display:block;font-size:13px;color:var(--ink)}
.call strong{display:block;font-size:21px;font-weight:500;color:var(--ink)}
/* hero */
.hero-title{left:110px;top:236px;font-size:54px;font-weight:700;color:var(--ink)}
.hero-lead{left:111px;top:308px;width:430px;font-size:14px;line-height:22px;color:#444}
.lead-form{left:111px;top:367px;width:450px;display:grid;grid-template-columns:repeat(3,140px);gap:15px 14px}
.field{height:36px;background:var(--white);border:1px solid #e8e2dc;font-size:12px;color:#555;padding:0 18px;display:flex;align-items:center}
.submit{height:36px;background:var(--red);color:var(--white);font-size:12px;font-weight:700;display:flex;align-items:center;justify-content:center}
.hero-photo{left:650px;top:205px;width:310px;height:430px;background:linear-gradient(180deg,#6e5b4f 0%,#3a3130 55%,#2c2a2a 100%);border-radius:120px 120px 0 0;opacity:.9}
.scroll-down{left:347px;top:720px;width:48px;height:48px;border-radius:50%;background:var(--white);border:2px solid var(--red);display:flex;align-items:center;justify-content:center}
/* section titles */
.section-title{left:0;width:1200px;text-align:center;font-size:42px;font-weight:700;color:var(--ink)}
.rule{width:54px;height:2px;background:var(--red)}
/* offers */
.offer-icon{border-radius:50%;display:flex;align-items:center;justify-content:center}
.offer-icon.main{left:557px;top:960px;width:86px;height:86px;background:var(--red)}
.offer-icon.side{width:86px;height:86px;background:var(--white);border:2px solid var(--red)}
.offer{width:290px;text-align:center}
.offer h3{font-size:17px;font-weight:500;color:var(--ink);margin-bottom:12px}
.offer p{font-size:14px;line-height:21.5px;color:var(--text)}
.offer-photo{left:413px;top:1205px;width:374px;height:374px;border-radius:50%;border:6px solid var(--red);background:radial-gradient(circle at 50% 40%,#f1f1f1 0%,#c9c6c3 55%,#3d3a3a 100%)}
/* about */
.about-bg{left:0;top:1693px;width:1200px;height:603px;background:var(--grey-bg)}
.accent{background:var(--red)}
.about-photo{left:112px;top:1809px;width:467px;height:378px;background:linear-gradient(135deg,#5a3f2d 0%,#2d2522 60%,#6b5748 100%)}
.about-title{left:626px;top:1784px;font-size:42px;font-weight:700;color:var(--ink)}
.about-copy{left:626px;top:1866px;width:463px;font-size:14px;line-height:21.5px;text-align:justify;color:var(--text)}
.about-copy p+p{margin-top:21px}
.btn{background:var(--red);color:var(--white);font-size:14px;font-weight:700;display:flex;align-items:center;justify-content:center}
/* testimonials */
.slide{background:linear-gradient(135deg,#e9e9ee 0%,#cfd2da 100%)}
.slide.main{left:352px;top:2511px;width:494px;height:285px;background:linear-gradient(180deg,#3a3a3a 0%,#5b4032 50%,#2b2b2b 100%)}
.play{border-radius:50%;background:var(--red);display:flex;align-items:center;justify-content:center}
.quote{font-size:90px;font-weight:700;color:var(--red);line-height:1;font-family:Georgia,serif}
.dot{width:11px;height:11px;border-radius:50%;background:#cfcfcf}
.dot.on{background:var(--red)}
/* videos */
.video-card{width:466px;height:338px;border:1px solid #ddd;background:linear-gradient(180deg,#fafafa 0%,#eeeeee 100%)}
.arrow-btn{width:44px;height:44px;border-radius:50%;background:#8a8a8a;display:flex;align-items:center;justify-content:center}
/* footer */
.footer{left:0;top:3706px;width:1200px;height:398px;background:var(--footer)}
.foot-h{font-size:21px;font-weight:700;color:var(--white)}
.foot-text{font-size:14px;line-height:26px;color:var(--footer-text)}
.links{list-style:none;font-size:14px;color:var(--footer-text)}
.links li{height:30.5px}
.social{width:30px;height:30px;border-radius:50%;border:1px solid #777}
.contact-row{display:flex;align-items:center;gap:16px;font-size:14px;color:var(--footer-text)}
.legal{font-size:13px;color:var(--footer-text)}
</style>
</head>
<body>

<!-- hero backdrop -->
<svg class="backdrop" width="1200" height="800" viewBox="0 0 1200 800" aria-hidden="true">
  <defs>
    <linearGradient id="heroGrad" x1="0" y1="0" x2="1" y2="1">
      <stop offset="0" stop-color="#f6e2cd"/>
      <stop offset="1" stop-color="#eed4b8"/>
    </linearGradient>
  </defs>
  <polygon points="0,0 1200,0 1200,566 383,742 0,566" fill="url(#heroGrad)"/>
  <polygon points="0,566 383,742 0,600" fill="#ececec"/>
  <polygon points="383,736 1200,560 1200,572 383,750" fill="var(--red)"/>
</svg>

<header>
  <div class="abs brand">Petros <span>Vandelis</span></div>
  <nav class="abs nav">
    <a class="active" href="#">Home</a><a href="#">About</a><a href="#">Offers</a><a href="#">Testimonials</a><a href="#">Contact us</a>
  </nav>
  <div class="abs call">
    <div class="call-icon"><svg width="16" height="16" viewBox="0 0 24 24"><path d="M6.6 10.8a15 15 0 006.6 6.6l2.2-2.2a1 1 0 011-.25 11.4 11.4 0 003.6.57 1 1 0 011 1V20a1 1 0 01-1 1A17 17 0 013 4a1 1 0 011-1h3.5a1 1 0 011 1c0 1.25.2 2.45.57 3.57a1 1 0 01-.25 1z" fill="var(--red)"/></svg></div>
    <div><small>Call Us Today :</small><strong>+1 888 888 8888</strong></div>
  </div>
</header>

<section class="hero">
  <h1 class="abs hero-title">Petros <span>Vandelis</span></h1>
  <p class="abs hero-lead">Lorem ipsum dolor sit amet, consectetur adipiscing elit, sed do tempor incididunt ut labore et dolore magna aliqua.</p>
  <form class="abs lead-form">
    <div class="field">Name</div><div class="field">Email</div><div class="field">Phone</div>
    <div class="field">Address</div><div class="field">Types of services</div><div class="submit">SUBMIT</div>
  </form>
  <div class="abs hero-photo" role="img" aria-label="Petros Vandelis speaking on stage with a microphone"></div>
  <div class="abs scroll-down"><svg width="18" height="20" viewBox="0 0 18 20"><path d="M9 2v15M3 11l6 6 6-6" stroke="#222" stroke-width="2" fill="none"/></svg></div>
</section>

<section class="offers">
  <h2 class="abs section-title" style="top:860px">Our Offers</h2>
  <div class="abs rule" style="left:573px;top:925px"></div>
  <svg class="abs" style="left:0;top:990px" width="1200" height="200" viewBox="0 990 1200 200" aria-hidden="true">
    <path d="M298 1140 Q600 870 905 1140" stroke="#333" stroke-width="2" stroke-dasharray="2 5" fill="none"/>
  </svg>
  <div class="abs offer-icon main">
    <svg width="44" height="40" viewBox="0 0 44 40"><circle cx="16" cy="11" r="6" fill="#fff"/><circle cx="29" cy="11" r="6" fill="#fff"/><path d="M4 36c0-8 6-13 12-13s12 5 12 13z" fill="#fff"/><path d="M18 36c0-8 5-13 11-13s11 5 11 13z" fill="#fff"/></svg>
  </div>
  <div class="abs offer" style="left:455px;top:1064px"><h3>Consulting/Mastermind</h3><p>Lorem ipsum dolor sit amet, consectetur adipiscing elit, sed do eiusmod tempor incididunt ut labore et dolor</p></div>

  <div class="abs offer-icon side" style="left:223px;top:1132px">
    <svg width="40" height="34" viewBox="0 0 40 34"><rect x="3" y="8" width="26" height="20" rx="2" fill="none" stroke="var(--red)" stroke-width="2.5"/><path d="M13 13l8 5-8 5z" fill="var(--red)"/><circle cx="32" cy="8" r="6" fill="var(--red)"/><line x1="3" y1="32" x2="29" y2="32" stroke="var(--red)" stroke-width="2.5"/></svg>
  </div>
  <div class="abs offer" style="left:121px;top:1235px"><h3>Paid ads</h3><p>Lorem ipsum dolor sit amet, consectetur adipiscing elit, sed do eiusmod tempor incididunt ut labore et dolor</p></div>

  <div class="abs offer-icon side" style="left:888px;top:1132px">
    <svg width="40" height="36" viewBox="0 0 40 36"><circle cx="9" cy="9" r="5" fill="var(--red)"/><path d="M2 34V20c0-3 3-5 7-5h5l6-5 2 2-7 7v15z" fill="var(--red)"/><rect x="20" y="4" width="18" height="14" fill="none" stroke="var(--red)" stroke-width="2.5"/><line x1="29" y1="18" x2="29" y2="30" stroke="var(--red)" stroke-width="2.5"/></svg>
  </div>
  <div class="abs offer" style="left:787px;top:1235px"><h3>Training</h3><p>Lorem ipsum dolor sit amet, consectetur adipiscing elit, sed do eiusmod tempor incididunt ut labore et dolor</p></div>

  <div class="abs offer-photo" role="img" aria-label="Studio interview between two men in front of a camera"></div>
</section>

<section class="about">
  <div class="abs about-bg"></div>
  <div class="abs accent" style="left:504px;top:1795px;width:89px;height:67px"></div>
  <div class="abs accent" style="left:96px;top:2136px;width:89px;height:69px"></div>
  <div class="abs about-photo" role="img" aria-label="Petros Vandelis with a fellow marketer at an event"></div>
  <h2 class="abs about-title">About Me</h2>
  <div class="abs rule" style="left:626px;top:1848px"></div>
  <div class="abs about-copy">
    <p>Lorem ipsum dolor sit amet, consectetur adipiscing elit, sed do eiusmod tempor incididunt ut labore et dolore magna aliqua. Ut enim ad minim veniam, quis nostrud exercitation ullamco laboris nisi ut aliquip ex ea commodo consequat. Duis aute irure dolor in reprehenderit in voluptate velit esse cillum dolore eu fugiat nulla pariatur.</p>
    <p>Excepteur sint occaecat cupidatat non proident, sunt in culpa qui officia deserunt mollit anim id est laborum. Lorem ipsum dolor sit amet, consectetur adipiscing elit, sed do eiusmod tempor incididunt ut labore et dolore magna aliqua. Ut enim ad minim veniam, quis nostrud exercitation ullamco laboris nisi ut aliquip ex ea commodo consequat. Duis aute irure dolor in reprehenderit in voluptate velit esse cillum dolore eu fugiat nulla pariatur.</p>
  </div>
  <div class="abs btn" style="left:626px;top:2166px;width:123px;height:35px">Learn More</div>
</section>

<section class="testimonials">
  <h2 class="abs section-title" style="top:2395px">Video Testimonials</h2>
  <div class="abs rule" style="left:573px;top:2460px"></div>
  <svg class="abs" style="left:0;top:2505px" width="1200" height="300" viewBox="0 0 1200 300" aria-hidden="true">
    <defs><linearGradient id="slideGrad" x1="0" y1="0" x2="1" y2="1"><stop offset="0" stop-color="#f0f0f4"/><stop offset="1" stop-color="#cfd1d8"/></linearGradient></defs>
    <polygon points="0,40 327,10 327,290 0,265" fill="url(#slideGrad)"/>
    <polygon points="869,10 1200,40 1200,265 869,290" fill="url(#slideGrad)"/>
  </svg>
  <div class="abs slide main" role="img" aria-label="Video testimonial recorded over an online store page"></div>
  <div class="abs quote" style="left:375px;top:2478px">“</div>
  <div class="abs quote" style="left:768px;top:2768px">”</div>
  <div class="abs play" style="left:574px;top:2626px;width:52px;height:52px"><svg width="18" height="20" viewBox="0 0 18 20"><path d="M2 1l15 9-15 9z" fill="#fff"/></svg></div>
  <div class="abs dot on" style="left:576px;top:2847px"></div>
  <div class="abs dot" style="left:597px;top:2847px"></div>
  <div class="abs dot" style="left:617px;top:2847px"></div>
</section>

<svg class="backdrop" style="top:2880px" width="1200" height="220" viewBox="0 0 1200 220" aria-hidden="true">
  <polygon points="0,20 1200,20 1200,24 367,212 0,110" fill="#f3f3f3"/>
  <polygon points="367,200 1200,18 1200,30 367,216" fill="var(--red)"/>
</svg>

<section class="videos">
  <h2 class="abs section-title" style="top:3158px">Our Videos</h2>
  <div class="abs rule" style="left:573px;top:3224px"></div>
  <div class="abs video-card" style="left:110px;top:3268px" role="img" aria-label="Video lesson walking through a product research spreadsheet"></div>
  <div class="abs video-card" style="left:623px;top:3268px" role="img" aria-label="Video lesson walking through a website analytics dashboard"></div>
  <div class="abs play" style="left:313px;top:3407px;width:60px;height:60px"><svg width="20" height="22" viewBox="0 0 18 20"><path d="M2 1l15 9-15 9z" fill="#fff"/></svg></div>
  <div class="abs play" style="left:826px;top:3407px;width:60px;height:60px"><svg width="20" height="22" viewBox="0 0 18 20"><path d="M2 1l15 9-15 9z" fill="#fff"/></svg></div>
  <div class="abs arrow-btn" style="left:37px;top:3431px"><svg width="10" height="14" viewBox="0 0 10 14"><path d="M8 1L2 7l6 6" stroke="#fff" stroke-width="2" fill="none"/></svg></div>
  <div class="abs arrow-btn" style="left:1121px;top:3431px"><svg width="10" height="14" viewBox="0 0 10 14"><path d="M2 1l6 6-6 6" stroke="#fff" stroke-width="2" fill="none"/></svg></div>
</section>

<footer class="abs footer">
  <h4 class="abs foot-h" style="left:112px;top:84px">Petros Vandelis</h4>
  <p class="abs foot-text" style="left:112px;top:127px;width:325px">Lorem ipsum dolor sit amet, consectetur adipiscing elit, sed do eiusmod tempor incididunt ut labore et dolore magna aliqua.</p>
  <div class="abs social" style="left:113px;top:230px" aria-label="Social profile"></div>
  <div class="abs social" style="left:156px;top:230px" aria-label="Social profile"></div>
  <div class="abs social" style="left:199px;top:230px" aria-label="Social profile"></div>

  <h4 class="abs foot-h" style="left:583px;top:84px">Quick Links</h4>
  <ul class="abs links" style="left:583px;top:131px">
    <li>Home</li><li>About us</li><li>Services</li><li>Blog</li><li>Contact</li>
  </ul>

  <h4 class="abs foot-h" style="left:873px;top:84px">Contact Us</h4>
  <div class="abs contact-row" style="left:874px;top:131px"><svg width="12" height="16" viewBox="0 0 12 16"><path d="M6 0a6 6 0 00-6 6c0 4.5 6 10 6 10s6-5.5 6-10a6 6 0 00-6-6z" fill="var(--red)"/><circle cx="6" cy="6" r="2" fill="var(--footer)"/></svg><span>Lorem ipsum dolor sit amet,</span></div>
  <div class="abs contact-row" style="left:874px;top:192px"><svg width="13" height="13" viewBox="0 0 24 24"><path d="M6.6 10.8a15 15 0 006.6 6.6l2.2-2.2a1 1 0 011-.25 11.4 11.4 0 003.6.57 1 1 0 011 1V20a1 1 0 01-1 1A17 17 0 013 4a1 1 0 011-1h3.5a1 1 0 011 1c0 1.25.2 2.45.57 3.57a1 1 0 01-.25 1z" fill="var(--red)"/></svg><span>+1 888 888 8888</span></div>
  <div class="abs contact-row" style="left:874px;top:253px"><svg width="14" height="11" viewBox="0 0 14 11"><rect width="14" height="11" rx="1" fill="var(--red)"/><path d="M1 1l6 5 6-5" stroke="var(--footer)" stroke-width="1.3" fill="none"/></svg><span>info@companyname.com</span></div>

  <p class="abs legal" style="left:112px;top:337px">© Copyrights 2023 Company name I All Rights Reserved</p>
  <p class="abs legal" style="left:974px;top:337px">Terms of Services</p>
  <p class="abs legal" style="left:1129px;top:337px">C38</p>
</footer>

</body>
</html>
```